Investment company needing business card

We are wanting a business card which looks sharp and easy on the eye. We are thinking of having a business card with the logo embossed on it, to really make it stand out. We will only have a small amount of information of the business card, person's name, position, email address and phone number

Contact Information for Business Card

Danielle Frost
Executive Assistant
+64 21 473 5162
danielf@harwickpartners.co.nz

Requirements
Must have
• Embossed logo
Should not have
• Not to be busy

```html
<!DOCTYPE html>
<html lang="en">
<head>
<meta charset="utf-8">
<title>Harwick Partners – Business Card</title>
<link rel="stylesheet" href="https://fonts.googleapis.com/css2?family=Lato:wght@300;400;700&display=swap">
<style>
  :root {
    --bg: #e9e7e3;
    --card: #f6f6f5;
    --green: #1fae78;
    --grey-dark: #5f6062;
    --grey-mid: #7a7b7d;
    --text-grey: #6d6e70;
    --rule: #8a8b8d;
  }
  * { margin: 0; padding: 0; box-sizing: border-box; }
  html, body {
    width: 1200px; height: 780px; overflow: hidden;
    background: var(--bg);
    font-family: "Lato", Arial, sans-serif;
  }
  .canvas {
    position: relative; width: 1200px; height: 780px;
    display: flex; align-items: center; justify-content: center;
  }
  .card {
    position: relative; width: 1000px; height: 572px;
    background: var(--card);
    box-shadow: 0 6px 20px rgba(0,0,0,0.18);
    overflow: hidden;
  }
  .card__shapes { position: absolute; inset: 0; }
  .brand {
    position: absolute; left: 250px; top: 120px;
    display: flex; align-items: center; gap: 18px;
  }
  .brand__mark {
    width: 54px; height: 54px; background: var(--green);
  }
  .brand__name {
    font-weight: 700; font-size: 46px; letter-spacing: 3px;
    color: var(--green); text-transform: uppercase; white-space: nowrap;
  }
  .brand__rule {
    position: absolute; left: 322px; top: 196px;
    width: 430px; height: 2px; background: var(--rule);
  }
  .contact {
    position: absolute; left: 250px; top: 380px;
    color: var(--text-grey);
  }
  .contact__name {
    font-weight: 700; font-size: 28px; color: var(--green); line-height: 1.1;
  }
  .contact__role {
    font-weight: 400; font-size: 22px; line-height: 1.2; margin-bottom: 26px;
  }
  .contact__line {
    display: flex; align-items: center; gap: 14px;
    font-weight: 300; font-size: 22px; line-height: 1.6;
  }
  .contact__icon { width: 20px; height: 20px; flex: none; }
</style>
</head>
<body>
<main class="canvas">
  <article class="card">
    <svg class="card__shapes" viewBox="0 0 1000 572" width="1000" height="572" aria-hidden="true">
      <path d="M0,0 H250 Q60,286 210,572 H0 Z" fill="var(--green)"/>
      <path d="M1000,0 H760 Q990,300 790,572 H1000 Z" fill="var(--grey-dark)"/>
      <path d="M760,0 H790 Q1010,300 820,572 H790 Q990,300 760,0 Z" fill="var(--grey-mid)" opacity="0.6"/>
    </svg>

    <div class="brand">
      <span class="brand__mark"></span>
      <span class="brand__name">Harwick Partners</span>
    </div>
    <div class="brand__rule"></div>

    <section class="contact">
      <p class="contact__name">Danielle Frost</p>
      <p class="contact__role">Executive Assistant</p>
      <p class="contact__line">
        <svg class="contact__icon" viewBox="0 0 20 20" aria-hidden="true">
          <rect x="5" y="1.5" width="10" height="17" rx="2" fill="none" stroke="var(--text-grey)" stroke-width="1.6"/>
          <line x1="8.5" y1="15.5" x2="11.5" y2="15.5" stroke="var(--text-grey)" stroke-width="1.4"/>
        </svg>
        +64 21 473 5162
      </p>
      <p class="contact__line">
        <svg class="contact__icon" viewBox="0 0 20 20" aria-hidden="true">
          <rect x="1.5" y="4" width="17" height="12" fill="var(--green)"/>
          <path d="M1.5,4 L10,11 L18.5,4" fill="none" stroke="#ffffff" stroke-width="1.4"/>
        </svg>
        danielf@harwickpartners.co.nz
      </p>
    </section>
  </article>
</main>
</body>
</html>
```